TalkHarbor - Language Coaching Services

Sleek, innovative, trendy design for Language Coaching business.

TalkHarbor is a new UK based company that provides Language Coaching services. We offer highly personalized on-line and face to face language courses. We also impart learning techniques workshops based on the latest neuroscience research for second-language acquisition.

Target Market(s)

See attached info

Industry/Entity Type

Consulting

Contact Information for Business Card

TalkHarbor
DaniaKV@talkharbor.co.uk
TalkHarbor.co.uk
London, UK

Font styles to use
Sans Serif

```html
<!DOCTYPE html>
<html lang="en">
<head>
<meta charset="utf-8">
<title>TalkHarbor Business Card</title>
<link href="https://fonts.googleapis.com/css2?family=Open+Sans:wght@300;400;600;700&display=swap" rel="stylesheet">
<style>
  :root {
    --brand-blue: #0f8fcb;
    --brand-blue-dark: #0a5f93;
    --brand-blue-light: #16b4ec;
    --ink-grey: #8a8f94;
    --ink-dark: #3d4247;
    --paper: #f7f8f8;
    --backdrop: #2a2c2f;
    --white: #ffffff;
  }
  * { box-sizing: border-box; margin: 0; padding: 0; }
  html, body {
    width: 1200px; height: 892px; overflow: hidden;
    background: var(--backdrop);
    font-family: "Open Sans", Arial, sans-serif;
  }
  .sheet {
    width: 1200px; height: 892px;
    display: flex; flex-direction: column; align-items: center;
    justify-content: space-evenly;
  }
  .card {
    width: 680px; height: 389px; position: relative; overflow: hidden;
    border-radius: 2px;
  }

  /* Back side */
  .card--back {
    background: radial-gradient(ellipse at 52% 48%, var(--brand-blue-light) 0%, var(--brand-blue) 45%, var(--brand-blue-dark) 100%);
    display: flex; flex-direction: column; align-items: center; justify-content: center; gap: 18px;
  }
  .back-ring {
    width: 150px; height: 150px; border-radius: 50%;
    border: 12px solid var(--white);
  }
  .back-name {
    color: var(--white); font-weight: 600; font-size: 30px; letter-spacing: 2px;
  }

  /* Front side */
  .card--front { background: var(--paper); }
  .brand {
    position: absolute; left: 70px; top: 92px; width: 250px;
    display: flex; flex-direction: column; align-items: center; gap: 16px;
  }
  .brand-mark {
    width: 96px; height: 96px; border-radius: 50%;
    border: 7px solid var(--brand-blue);
  }
  .brand-name {
    color: var(--brand-blue); font-weight: 600; font-size: 30px; letter-spacing: 1px;
  }
  .divider {
    position: absolute; left: 345px; top: 48px; width: 1px; height: 150px;
    background: linear-gradient(to bottom, transparent, #b9bdc0, transparent);
  }
  .contact { position: absolute; left: 375px; top: 50px; }
  .contact-name {
    color: var(--brand-blue); font-weight: 700; font-size: 24px; line-height: 1.1;
  }
  .contact-title {
    color: var(--ink-grey); font-weight: 300; font-size: 17px; letter-spacing: 0.5px; margin-bottom: 10px;
  }
  .contact-line {
    display: flex; align-items: center; gap: 10px;
    color: var(--ink-dark); font-size: 17px; line-height: 1.5;
  }
  .contact-line svg { width: 16px; height: 16px; flex: none; }
  .band {
    position: absolute; left: 0; right: 0; top: 268px; height: 46px;
    background: var(--brand-blue);
    display: flex; align-items: center; justify-content: center;
  }
  .band-url {
    color: var(--white); font-size: 18px; letter-spacing: 6px;
  }
  .band-dot {
    position: absolute; right: 26px; top: 7px; width: 32px; height: 32px;
    border-radius: 50%; border: 3px solid var(--white);
  }
</style>
</head>
<body>
<main class="sheet">
  <section class="card card--back" aria-label="Card back">
    <div class="back-ring"></div>
    <div class="back-name">TalkHarbor</div>
  </section>

  <section class="card card--front" aria-label="Card front">
    <div class="brand">
      <div class="brand-mark"></div>
      <div class="brand-name">TALKHARBOR</div>
    </div>
    <div class="divider"></div>
    <div class="contact">
      <div class="contact-name">DANIA VALE</div>
      <div class="contact-title">PRESIDENT</div>
      <div class="contact-line">
        <svg viewBox="0 0 16 16" aria-hidden="true"><rect x="4" y="1" width="8" height="14" rx="1.5" fill="none" stroke="#0f8fcb" stroke-width="1.6"/><circle cx="8" cy="12.5" r="0.9" fill="#0f8fcb"/></svg>
        <span>020 7946 0321</span>
      </div>
      <div class="contact-line">
        <svg viewBox="0 0 16 16" aria-hidden="true"><rect x="1" y="3" width="14" height="10" fill="#0f8fcb"/><path d="M1 3 L8 9 L15 3" fill="none" stroke="#fff" stroke-width="1.2"/></svg>
        <span>DaniaKV@talkharbor.co.uk</span>
      </div>
    </div>
    <div class="band">
      <span class="band-url">www.talkharbor.co.uk</span>
      <div class="band-dot"></div>
    </div>
  </section>
</main>
</body>
</html>
```